Business card design for holistic health care clinic

We need a double-sided business card design for our holistic health care clinic that integrates our logo design and also its color scheme. My business is called Valmira. It is an integrative medicine clinic. You have already done the logo for me. Please ensure an elegant and upscale design that is not cluttered, but still has all the necessary information (please see below for details).

Target Market(s)

Wellness, fitness, rehabilitation for educated, well-traveled open-minded clients who are focused on natural, organic, balanced and preventive healthcare and lifestyle.

Industry/Entity Type

Medical

Contact Information for Business Card

Modern, clean.

Number of Pages Required

1 page

Font styles to use
Serif
Sans Serif

Colors

Designer to choose colors to be used in the design.

Requirements
Must have
• Logo on one side, all other information on the other side.
• Other information should include:
• Tobias Wrenfeld - DOE, CPT, LMT
• 4100 East Marrow Drive
• Austin, TX 78119
• 512 555 0148
• 818 555 0192
• info@ValmiraHealth.example
• t.wrenfeld@ValmiraHealth.example
Nice to have
• Darker background on front - but not totally black - shaded/dark gray.

```html
<!DOCTYPE html>
<html lang="en">
<head>
<meta charset="utf-8">
<title>Valmira Business Card</title>
<link href="https://fonts.googleapis.com/css2?family=Nunito:wght@800&family=Roboto:ital,wght@0,400;1,400&family=Roboto+Condensed:wght@700&display=swap" rel="stylesheet">
<style>
  :root {
    --backdrop: #e4e4e4;
    --card-dark: #2a2a2a;
    --card-light: #f4f4f4;
    --brand-blue: #1a8fd0;
    --text-light: #f2f2f2;
    --text-dark: #2b2b2b;
    --text-muted: #555555;
    --rule: #6a6a6a;
  }
  * { margin: 0; padding: 0; box-sizing: border-box; }
  html, body {
    width: 1200px; height: 960px; overflow: hidden;
    background: var(--backdrop);
  }
  .canvas { position: relative; width: 1200px; height: 960px; }

  .card { position: absolute; overflow: hidden; }
  .card-front {
    left: 314px; top: 113px; width: 602px; height: 343px;
    background: var(--card-dark);
  }
  .card-back {
    left: 311px; top: 472px; width: 600px; height: 343px;
    background: var(--card-light);
  }

  .profile-band { position: absolute; left: 0; top: 0; }

  .brand-name {
    font-family: "Nunito", sans-serif;
    font-weight: 800;
    color: var(--brand-blue);
    letter-spacing: 1px;
    line-height: 1;
  }
  .brand-tagline {
    font-family: "Nunito", sans-serif;
    font-weight: 800;
    color: var(--brand-blue);
    line-height: 1;
  }

  .front-logo { position: absolute; left: 48px; top: 82px; }
  .front-logo .brand-name { font-size: 50px; }
  .front-logo .brand-tagline { font-size: 15.5px; margin-top: 6px; }

  .address {
    position: absolute; left: 49px; top: 182px;
    font-family: "Roboto", sans-serif; font-size: 14.5px;
    color: var(--text-light); line-height: 18px;
  }
  .contact-list {
    position: absolute; left: 49px; top: 229px; list-style: none;
    font-family: "Roboto", sans-serif; font-size: 14.5px;
    color: var(--text-light);
  }
  .contact-list li { display: flex; align-items: center; height: 19px; }
  .contact-list svg { width: 13px; height: 13px; margin-right: 10px; fill: var(--brand-blue); }

  .person {
    position: absolute; right: 50px; top: 267px; text-align: right;
    font-family: "Roboto Condensed", sans-serif; font-weight: 700;
    color: var(--text-dark); white-space: nowrap;
  }
  .person-name { font-size: 19px; line-height: 22px; }
  .person-credentials { font-size: 12px; line-height: 16px; }

  .back-logo {
    position: absolute; left: 0; right: 0; top: 132px; text-align: center;
  }
  .back-logo .brand-name { font-size: 62px; }
  .back-logo .brand-tagline { font-size: 18.5px; margin-top: 8px; }

  .slogan {
    position: absolute; left: 88px; right: 88px; top: 284px;
    display: flex; align-items: center; gap: 8px;
    font-family: "Roboto", sans-serif; font-style: italic; font-size: 17px;
    color: var(--text-muted); white-space: nowrap;
  }
  .slogan::before, .slogan::after {
    content: ""; flex: 1; height: 1px; background: var(--rule);
  }
</style>
</head>
<body>
<div class="canvas">

  <section class="card card-front">
    <svg class="profile-band" width="602" height="343" viewBox="0 0 602 343" role="img" aria-label="Blue flowing shape with human profile silhouette illustration">
      <path d="M597,0 L602,0 L602,343 L290,343 C335,328 358,300 366,255 C376,195 398,158 450,128 C520,88 585,70 597,0 Z" fill="var(--brand-blue)"/>
    </svg>

    <div class="front-logo">
      <div class="brand-name">VALMIRA</div>
      <div class="brand-tagline">Integrative Holistic Medicine</div>
    </div>

    <div class="address">
      <p>4100 East Marrow Drive</p>
      <p>Austin, TX 78119</p>
    </div>

    <ul class="contact-list">
      <li><svg viewBox="0 0 16 16"><path d="M3.5 1 6 3.5 4.6 5.6c.9 2.3 3.5 4.9 5.8 5.8L12.5 10 15 12.5 13 15C6.8 14.5 1.5 9.2 1 3z"/></svg>512 555 0148</li>
      <li><svg viewBox="0 0 16 16"><path d="M4.5 0h7A1.5 1.5 0 0 1 13 1.5v13a1.5 1.5 0 0 1-1.5 1.5h-7A1.5 1.5 0 0 1 3 14.5v-13A1.5 1.5 0 0 1 4.5 0zM5 2v10h6V2zm3 11a1 1 0 1 0 0 2 1 1 0 0 0 0-2z"/></svg>818 555 0192</li>
      <li><svg viewBox="0 0 16 16"><path d="M1 3h14v1.2L8 9 1 4.2zm0 2.6 7 4.8 7-4.8V13H1z"/></svg>t.wrenfeld@ValmiraHealth.example</li>
      <li><svg viewBox="0 0 16 16"><path d="M8 1a7 7 0 1 0 0 14A7 7 0 0 0 8 1zm0 1.5c.8 0 1.8 1.6 2.1 4.5H5.9C6.2 4.1 7.2 2.5 8 2.5zM2.6 8.6h2.2c.1 1.8.5 3.3 1 4.3a5.5 5.5 0 0 1-3.2-4.3zm0-1.6a5.5 5.5 0 0 1 3.2-3.9c-.5 1-.9 2.4-1 3.9zm5.4 6.5c-.8 0-1.8-1.6-2.1-4.9h4.2c-.3 3.3-1.3 4.9-2.1 4.9zm2.2-.6c.5-1 .9-2.5 1-4.3h2.2a5.5 5.5 0 0 1-3.2 4.3zm1-5.9c-.1-1.5-.5-2.9-1-3.9A5.5 5.5 0 0 1 13.4 7z"/></svg>www.ValmiraHealth.example</li>
    </ul>

    <div class="person">
      <div class="person-name">TOBIAS WRENFELD</div>
      <div class="person-credentials">DOE, CPT, LMT</div>
    </div>
  </section>

  <section class="card card-back">
    <div class="back-logo">
      <div class="brand-name">VALMIRA</div>
      <div class="brand-tagline">Integrative Holistic Medicine</div>
    </div>
    <p class="slogan">helping the body help itself</p>
  </section>

</div>
</body>
</html>
```